Business card design needed

I need a business card design for a dog walking, dog minding and dog training business. Please refer to my website for the basic company colours and fonts I'm after. Planning on a double sided card, so all information doesn't need to be on the 'front' side.
Cheers

Industry/Entity Type

Dog Training

Contact Information for Business Card

Bramble Paws - gathering hounds
Rua 0498376214
bramblepaws.com.au
-walking
-holiday stays
-onsite care
-training and behavioural consultations

```html
<!DOCTYPE html>
<html lang="en">
<head>
<meta charset="utf-8">
<title>Bramble Paws – Business Card</title>
<link href="https://fonts.googleapis.com/css2?family=Arvo:wght@700&family=Arimo&family=Tinos&family=Great+Vibes&display=swap" rel="stylesheet">
<style>
  :root {
    --backdrop-light: #f4f4f4;
    --backdrop-dark: #bdbdbd;
    --card-white: #ffffff;
    --card-black-top: #3a3838;
    --card-black-bottom: #161515;
    --brand-orange: #d9531e;
    --text-dark: #1c1c1c;
    --text-light: #f2f2f2;
    --paw-grey: #9a9a9a;
    --photo-warm: #b98d66;
    --photo-light: #e9e2da;
  }
  * { box-sizing: border-box; margin: 0; padding: 0; }
  html, body { width: 1200px; height: 827px; overflow: hidden; }
  body {
    background: radial-gradient(ellipse at 50% 35%, var(--backdrop-light) 0%, #dcdcdc 60%, var(--backdrop-dark) 100%);
    position: relative;
  }
  .card {
    position: absolute;
    width: 500px;
    height: 300px;
    border-radius: 22px;
    overflow: hidden;
    box-shadow: 0 6px 18px rgba(0,0,0,0.25);
  }

  /* Back side */
  .card-back {
    left: 70px;
    top: 264px;
    background: linear-gradient(180deg, var(--card-black-top), var(--card-black-bottom));
    color: var(--text-light);
  }
  .services {
    position: absolute;
    top: 38px;
    left: 0;
    width: 100%;
    text-align: center;
    list-style: none;
    font-family: "Tinos", serif;
    font-variant: small-caps;
    font-size: 17px;
    letter-spacing: 1.5px;
    line-height: 21px;
  }
  .paw-cluster-back {
    position: absolute;
    left: 34px;
    top: 176px;
    width: 90px;
    height: 80px;
    border-radius: 10px;
    background: linear-gradient(135deg, #6a6a6a, #3c3c3c);
  }
  .owner-name {
    position: absolute;
    left: 150px;
    top: 214px;
    font-family: "Great Vibes", cursive;
    font-size: 46px;
    color: var(--brand-orange);
  }
  .contact {
    position: absolute;
    left: 236px;
    top: 216px;
    font-family: "Arimo", sans-serif;
    font-size: 15px;
    line-height: 24px;
    list-style: none;
  }
  .contact li { display: flex; align-items: center; gap: 6px; }
  .contact svg { width: 12px; height: 14px; }

  /* Front side */
  .card-front {
    left: 630px;
    top: 264px;
    background: var(--card-white);
  }
  .dog-photo {
    position: absolute;
    left: 30px;
    top: 10px;
    width: 440px;
    height: 98px;
    border-radius: 8px;
    background: linear-gradient(90deg, #4a4a4a 0%, var(--photo-light) 30%, #f1ede6 50%, var(--photo-warm) 75%, #9b5532 100%);
  }
  .brand-rule {
    position: absolute;
    left: 0;
    top: 78px;
    width: 100%;
    height: 6px;
    background: var(--brand-orange);
  }
  .brand-name {
    position: absolute;
    left: 0;
    top: 150px;
    width: 100%;
    text-align: center;
    font-family: "Arvo", serif;
    font-weight: 700;
    font-size: 46px;
    letter-spacing: 1px;
    color: var(--brand-orange);
  }
  .tagline {
    position: absolute;
    left: 0;
    top: 214px;
    width: 100%;
    text-align: center;
    font-family: "Arimo", sans-serif;
    font-size: 22px;
    color: var(--text-dark);
  }
  .paw-cluster-front {
    position: absolute;
    right: 22px;
    bottom: 24px;
    width: 64px;
    height: 74px;
    border-radius: 10px;
    background: linear-gradient(135deg, #e2e2e2, #7a7a7a);
  }
</style>
</head>
<body>

  <section class="card card-back" aria-label="Card back">
    <ul class="services">
      <li>Walking</li>
      <li>Holiday stays</li>
      <li>Onsite care</li>
      <li>Training</li>
      <li>&amp;</li>
      <li>Behavioural Consultations</li>
    </ul>
    <div class="paw-cluster-back" role="img" aria-label="Cluster of grey paw print motifs"></div>
    <div class="owner-name">Rua</div>
    <ul class="contact">
      <li>
        <svg viewBox="0 0 12 14" aria-hidden="true"><rect x="2" y="0.5" width="8" height="13" rx="1.5" fill="none" stroke="#f2f2f2" stroke-width="1.2"/><rect x="3.5" y="2.5" width="5" height="5" fill="#f2f2f2"/></svg>
        <span>: 049-837-6214</span>
      </li>
      <li>
        <svg viewBox="0 0 12 14" aria-hidden="true"><rect x="0.5" y="1.5" width="11" height="11" rx="1" fill="#f2f2f2"/><text x="6" y="10" text-anchor="middle" font-size="8" font-family="Arimo, sans-serif" fill="#1c1c1c">W</text></svg>
        <span>: www.bramblepaws.com.au</span>
      </li>
    </ul>
  </section>

  <section class="card card-front" aria-label="Card front">
    <div class="dog-photo" role="img" aria-label="Photo of five dogs of different breeds peeking over an orange rail"></div>
    <div class="brand-rule"></div>
    <h1 class="brand-name">BRAMBLE PAWS</h1>
    <p class="tagline">gathering hounds</p>
    <div class="paw-cluster-front" role="img" aria-label="Trail of grey paw print motifs"></div>
  </section>

</body>
</html>
```